Wordpress theme website for professionals working together

My partner and I are offering business services, my wife in the energy business as mainly as member of the board of commissioners. I am working as interim manager/consultant in the accounting and finance area. Both activities are connected in one company VELMOT BV (dutch ltd). We need a CV based website. Beside this we do some financial and accounting services.

Target Market(s)

small medium business

Font styles to use
Sans Serif

Colors

Designer to choose colors to be used in the design.

Requirements
Must have
• Pictures of both members.
• CLEAN AND SIMPLE
• I LIKE BLACK & WHITE
Nice to have
• I like design like this theme: http://theme.pruxelo-example.com/resume/

```html
<!DOCTYPE html>
<html lang="en">
<head>
<meta charset="utf-8">
<title>Velmot BV — Contact</title>
<link rel="stylesheet" href="https://fonts.googleapis.com/css2?family=Montserrat:wght@400;500;600;700;800&family=Open+Sans:wght@400;600&display=swap">
<style>
:root{
  --ink:#000;
  --white:#fff;
  --paper:#eeeeee;
  --text:#222;
  --muted:#555;
  --nav:#555;
  --footer-link:#b5b5b5;
  --rule:#2c2c2c;
  --accent:#c40d0d;
  --logo:#153a78;
  --map:#e3e3e3;
}
*{box-sizing:border-box;margin:0;padding:0}
html,body{width:1200px;height:809px;overflow:hidden;background:var(--white)}
body{position:relative;font-family:'Open Sans',sans-serif;color:var(--text)}
.site-header{position:absolute;left:0;top:0;width:1200px;height:64px;background:var(--white);border-bottom:1px solid #ddd}
.brand{position:absolute;left:172px;top:20px;display:flex;align-items:center;gap:8px;font-family:'Montserrat',sans-serif;font-weight:700;font-size:26px;color:var(--logo);letter-spacing:-.5px}
.brand-mark{width:14px;height:14px;background:var(--accent)}
.main-nav{position:absolute;right:173px;top:28px;display:flex;gap:28.5px;font-family:'Montserrat',sans-serif;font-weight:500;font-size:11.2px;letter-spacing:1.1px;color:var(--nav)}
.main-nav .is-active{color:#111;font-weight:600}
.contact{position:absolute;left:0;top:65px;width:1200px;height:456px;background:var(--paper)}
.contact-map{position:absolute;left:172px;top:40px;width:856px;height:410px;border-radius:40%;background:radial-gradient(ellipse at center,var(--map) 0%,rgba(227,227,227,.5) 55%,rgba(238,238,238,0) 75%)}
.contact-title{position:absolute;left:0;width:1200px;top:64px;text-align:center;font-family:'Montserrat',sans-serif;font-weight:700;font-size:30px;color:var(--ink);letter-spacing:.3px}
.contact-intro{position:absolute;left:300px;width:600px;top:127px;text-align:center;font-size:11.6px;line-height:19px;color:#111}
.info-block{position:absolute}
.info-icon{position:absolute;left:0;top:0}
.info-heading{position:absolute;font-family:'Montserrat',sans-serif;font-weight:500;font-size:17px;color:#222;white-space:nowrap}
.info-lines{position:absolute;font-size:12.6px;line-height:21.8px;color:var(--muted);white-space:nowrap}
.btn-request{position:absolute;left:478px;top:360px;width:244px;height:37px;border-radius:19px;background:var(--ink);color:var(--white);font-family:'Montserrat',sans-serif;font-weight:600;font-size:11.3px;letter-spacing:.4px;display:flex;align-items:center;justify-content:center}
.site-footer{position:absolute;left:0;top:521px;width:1200px;height:288px;background:var(--ink);color:var(--white)}
.footer-col{position:absolute;top:35px}
.footer-col h3{font-family:'Montserrat',sans-serif;font-weight:500;font-size:20px;color:var(--white);margin-bottom:14px}
.footer-col ul{list-style:none;font-size:11px;line-height:20.3px;color:var(--footer-link);margin-left:1px}
.newsletter-form{position:absolute;left:708px;top:74px;width:320px;height:33px;border-radius:17px;background:#f2f2f2;overflow:hidden}
.newsletter-form .field{position:absolute;left:11px;top:9px;font-size:10.5px;color:#888}
.newsletter-form .btn-signup{position:absolute;right:0;top:0;width:85px;height:33px;background:var(--accent);color:var(--white);font-family:'Montserrat',sans-serif;font-weight:500;font-size:12.5px;display:flex;align-items:center;justify-content:center;border-radius:0 17px 17px 0}
.social{position:absolute;left:708px;top:135px;display:flex;gap:24px}
.social span{display:block;width:24px;height:24px;border-radius:50%;background:var(--white)}
.footer-rule{position:absolute;left:172px;top:228px;width:856px;height:1px;background:var(--rule)}
.copyright{position:absolute;left:0;width:1200px;top:252px;text-align:center;font-size:12px;color:#eee}
</style>
</head>
<body>
<header class="site-header">
  <div class="brand"><span>Velmot</span><span class="brand-mark"></span></div>
  <nav class="main-nav">
    <span class="is-active">HOME</span><span>MARIT</span><span>SKILLS</span><span>EXPERIENCE</span><span>PORTFOLIO</span><span>EDUCATION</span><span>CONTACT</span>
  </nav>
</header>

<section class="contact">
  <div class="contact-map" role="img" aria-label="Faint dotted world map in the background"></div>
  <h1 class="contact-title">CONTACT INFORMATION</h1>
  <p class="contact-intro">Sed ut perspiciatis unde omnis iste ntus error sit voluptatem accusa ntiumdolor emque laudantium, totam remd ut perspiciatis unde omnis iste nats error sit voluptatem accusa ntiumdolor emque lauda</p>

  <div class="info-block" style="left:380px;top:205px">
    <svg class="info-icon" width="18" height="24" viewBox="0 0 18 24" fill="none" stroke="#333" stroke-width="1.3"><path d="M9 23C9 23 1 13.5 1 8.5a8 8 0 0 1 16 0C17 13.5 9 23 9 23Z"/><circle cx="9" cy="8.5" r="3"/></svg>
    <div class="info-heading" style="left:30px;top:-3px">Address</div>
    <div class="info-lines" style="left:30px;top:28px">VELMOT BV<br>Lorem ipsmh Lore dummy<br>Dummy location 8758 dumm<br>KL42 7QX dummy citt</div>
  </div>

  <div class="info-block" style="left:627px;top:208px">
    <svg class="info-icon" width="21" height="15" viewBox="0 0 21 15" fill="none" stroke="#333" stroke-width="1.3"><rect x=".7" y=".7" width="19.6" height="13.6"/><path d="M.7 .7 10.5 8.5 20.3 .7M.7 14.3l7-6.5M20.3 14.3l-7-6.5"/></svg>
    <div class="info-heading" style="left:30px;top:-6px">Email</div>
    <div class="info-lines" style="left:30px;top:20px">info@velmot-example.com</div>
  </div>

  <div class="info-block" style="left:627px;top:275px">
    <svg class="info-icon" width="19" height="19" viewBox="0 0 19 19" fill="none" stroke="#333" stroke-width="1.2"><path d="M4.5 1.2 7.3 4.8 5.4 7.2c1.2 2.5 3.6 5 6.4 6.4l2.4-1.9 3.6 2.8-1.8 3C9 17.3 1.7 10 1.5 3Z"/></svg>
    <div class="info-heading" style="left:30px;top:-6px">Phone</div>
    <div class="info-lines" style="left:30px;top:20px">01632 960412, 01632 960413</div>
  </div>

  <div class="btn-request">REQUEST FOR INFORMATION</div>
</section>

<footer class="site-footer">
  <div class="footer-col" style="left:172px"><h3>Company</h3><ul><li>Sed ut perspiciatis</li><li>Unde omnis iste</li><li>Voluptatem</li><li>Accusantium</li><li>Doloremque</li><li>Laudantium</li></ul></div>
  <div class="footer-col" style="left:352px"><h3>About</h3><ul><li>Sed ut perspiciatis</li><li>Unde omnis iste</li><li>Voluptatem</li><li>Accusantium</li><li>Doloremque</li><li>Laudantium</li></ul></div>
  <div class="footer-col" style="left:517px"><h3>Links</h3><ul><li>Sed ut perspiciatis</li><li>Unde omnis iste</li><li>Voluptatem</li><li>Accusantium</li><li>Doloremque</li><li>Laudantium</li></ul></div>
  <div class="footer-col" style="left:708px"><h3>Newsletter</h3></div>
  <div class="newsletter-form"><span class="field">Email:</span><span class="btn-signup">SIGN UP</span></div>
  <div class="social" aria-label="Social links"><span></span><span></span><span></span><span></span></div>
  <div class="footer-rule"></div>
  <p class="copyright">© 2018 All Rights Are Reserved.Terms of Use &nbsp;|&nbsp; Privacy Policy</p>
</footer>
</body>
</html>
```